HARBORLINE AUTO GLASS

Mobile Glass Shop:

1) Windshield REPAIR 2)Windshield replacment 3) Rear Windshield Replacment 4) Side Window Replacment 5) car window replacment 6) Power Window Repair.

Schedual a service within 24 hour with one of our certified technicians.
Updates

See "brightvane auto repair" web site for referance on the nature of our buisness and service. www.brightvane-example.com

Coding

```html
<!DOCTYPE html>
<html lang="en">
<head>
<meta charset="utf-8">
<title>Harborline Auto Glass</title>
<link href="https://fonts.googleapis.com/css2?family=Bebas+Neue&family=Oswald:wght@600&family=Roboto:wght@400;500&display=swap" rel="stylesheet">
<style>
:root{
  --blue:#0a8ad6;
  --blue-deep:#0d5a9c;
  --navy:#0b3f73;
  --ink:#111;
  --text:#4a4a4a;
  --pale:#cfe3f3;
  --white:#fff;
  --footer:#000;
}
*{box-sizing:border-box;margin:0;padding:0}
html,body{width:1200px;height:3267px;overflow:hidden}
body{font-family:"Roboto",sans-serif;color:var(--text);background:var(--white);position:relative}
.btn{position:absolute;display:flex;align-items:center;justify-content:center;background:var(--blue);color:var(--white);font-family:"Oswald",sans-serif;font-weight:600;font-size:17px;letter-spacing:.2px;text-transform:uppercase;border-radius:2px}
.heading{font-family:"Oswald",sans-serif;font-weight:600;color:var(--blue-deep)}

/* header */
.site-header{position:absolute;left:0;top:0;width:1200px;height:115px;background:var(--white)}
.brand{position:absolute;display:flex;align-items:center;gap:10px;font-family:"Oswald",sans-serif;font-weight:600;line-height:1}
.brand .mark{width:26px;height:26px;background:currentColor}
.brand .name{display:flex;flex-direction:column}
.brand .l1{font-size:30px}
.brand .l2{font-size:13px;letter-spacing:4px;margin-top:3px}
.site-header .brand{left:112px;top:33px;color:var(--blue-deep)}
.nav{position:absolute;top:49px;font-family:"Roboto",sans-serif;font-weight:500;font-size:15px;color:#222}
.search{position:absolute;left:848px;top:48px}
.book{left:906px;top:34px;width:181px;height:50px;font-size:16px;gap:8px}

/* hero */
.hero{position:absolute;left:0;top:115px;width:1200px;height:729px;background:linear-gradient(120deg,#13609f 0%,#0f5592 55%,#1a6fb0 100%);overflow:hidden}
.hero h1{position:absolute;left:110px;top:140px;font-family:"Bebas Neue",sans-serif;font-weight:400;font-size:104px;line-height:110px;color:var(--white)}
.hero p{position:absolute;left:111px;top:370px;width:500px;font-size:20px;line-height:30px;color:var(--white)}
.hero .btn{left:112px;top:466px;width:157px;height:49px}
.dots{position:absolute;left:111px;top:553px;display:flex;gap:8px}
.dots span{width:22px;height:22px;border-radius:50%;border:2px solid var(--white)}
.dots span.on{background:var(--blue);border-color:var(--blue)}
.hero svg{position:absolute;left:0;top:0}

/* about */
.about-photo{position:absolute;left:188px;top:930px}
.about h2{position:absolute;left:599px;top:920px;font-size:34px}
.about p{position:absolute;left:599px;top:992px;width:490px;font-size:15.8px;line-height:25.7px}
.about .btn{left:599px;top:1201px;width:158px;height:49px}

/* services */
.services{position:absolute;left:0;top:1399px;width:1200px;height:942px;background:linear-gradient(160deg,#c6ddf0 0%,#d6e7f5 40%,#bcd6ec 100%)}
.services h2{position:absolute;left:0;width:1200px;top:78px;text-align:center;font-size:34px}
.card{position:absolute;width:303px;height:326px;background:var(--white);border-bottom:4px solid var(--blue-deep);text-align:center;box-shadow:0 2px 8px rgba(0,0,0,.06)}
.card svg{position:absolute;left:111px;top:38px}
.card h3{position:absolute;left:0;width:100%;top:119px;font-family:"Oswald",sans-serif;font-weight:600;font-size:23px;color:var(--ink)}
.card p{position:absolute;left:0;width:100%;top:170px;font-size:15.5px;line-height:28px}
.card .btn{left:73px;top:241px;width:158px;height:49px}

/* testimonials */
.testimonials h2{position:absolute;left:0;width:1200px;top:2414px;text-align:center;font-size:34px}
.quote{position:absolute;top:2496px;width:463px;height:310px;background:var(--white);box-shadow:0 0 18px rgba(0,0,0,.08)}
.quote .qm{position:absolute;left:14px;top:18px}
.quote p{position:absolute;left:58px;top:40px;width:376px;font-size:12.5px;line-height:21.8px;letter-spacing:-.1px;color:#444}
.quote .avatar{position:absolute;left:58px;top:222px;width:63px;height:63px;border-radius:50%;background:linear-gradient(135deg,#d9cfc4,#9a8f86)}
.quote .who{position:absolute;left:140px;top:228px;font-family:"Oswald",sans-serif;font-weight:600;font-size:18px;color:var(--ink)}
.quote .role{position:absolute;left:140px;top:259px;font-size:16px;color:#888}
.arrow{position:absolute;top:2604px;width:63px;height:63px;border-radius:50%;display:flex;align-items:center;justify-content:center}

/* footer */
.site-footer{position:absolute;left:0;top:2892px;width:1200px;height:375px;background:var(--footer);color:var(--white)}
.site-footer .brand{left:114px;top:115px;color:var(--white)}
.site-footer .brand .l1{font-size:38px}
.site-footer .brand .l2{font-size:15px;letter-spacing:5px}
.social{position:absolute;top:217px;display:flex;gap:15px;left:113px}
.social span{width:40px;height:40px;border-radius:50%;background:var(--white)}
.fcol{position:absolute;top:80px}
.fcol h4{font-family:"Oswald",sans-serif;font-weight:600;font-size:18px;margin-bottom:22px}
.links li{list-style:none;font-size:16px;line-height:28.4px}
.contact .row{display:flex;gap:14px;font-size:16px;line-height:26px;margin-bottom:13px}
.contact svg{flex:none;margin-top:4px}
.news{position:absolute;left:864px;top:132px;width:224px;height:40px;background:var(--white);border-radius:4px;overflow:hidden}
.news span{position:absolute;left:14px;top:11px;font-size:15px;color:#888}
.news .go{position:absolute;right:0;top:0;width:54px;height:40px;background:var(--blue-deep);display:flex;align-items:center;justify-content:center}
.copy{position:absolute;left:0;width:1200px;top:314px;text-align:center;font-size:15.5px}
</style>
</head>
<body>

<header class="site-header">
  <div class="brand"><span class="mark"></span><span class="name"><span class="l1">HARBORLINE</span><span class="l2">AUTO GLASS</span></span></div>
  <span class="nav" style="left:382px">HOME</span>
  <span class="nav" style="left:472px">ABOUT</span>
  <span class="nav" style="left:567px">SERVICES</span>
  <span class="nav" style="left:684px">MY APPOINTMENT</span>
  <svg class="search" width="20" height="20" viewBox="0 0 20 20"><circle cx="8" cy="8" r="6" fill="none" stroke="#0d5a9c" stroke-width="3"/><line x1="12.5" y1="12.5" x2="18" y2="18" stroke="#0d5a9c" stroke-width="3" stroke-linecap="round"/></svg>
  <div class="btn book"><svg width="15" height="15" viewBox="0 0 15 15"><rect x="1" y="2.5" width="13" height="11.5" fill="none" stroke="#fff" stroke-width="1.6"/><line x1="1" y1="6" x2="14" y2="6" stroke="#fff" stroke-width="1.6"/><line x1="4.5" y1="0.5" x2="4.5" y2="3.5" stroke="#fff" stroke-width="1.6"/><line x1="10.5" y1="0.5" x2="10.5" y2="3.5" stroke="#fff" stroke-width="1.6"/></svg>BOOK A SCHEDULE</div>
</header>

<section class="hero">
  <svg width="1200" height="729" viewBox="0 0 1200 729">
    <defs><linearGradient id="heroPhoto" x1="0" y1="0" x2="1" y2="1"><stop offset="0" stop-color="#3f8fc0"/><stop offset=".45" stop-color="#6e8ea8"/><stop offset="1" stop-color="#2e4e6e"/></linearGradient></defs>
    <path d="M1110 0 C930 100 760 130 632 150 C628 400 690 590 776 729 L1200 729 L1200 0 Z" fill="#fff"/>
    <path d="M658 178 C850 150 1050 110 1200 0 L1200 729 L810 729 C735 600 668 420 658 178 Z" fill="url(#heroPhoto)" role="img" aria-label="Technicians fitting a new windshield onto a car in a workshop"/>
  </svg>
  <h1>HARBORLINE<br>AUTO GLASS</h1>
  <p>Lorem ipsum dolor sit amet, consectetur adipiscing elit, sed do eiusmod tempor incididunt ut aliqua.</p>
  <div class="btn">GET STARTED</div>
  <div class="dots"><span class="on"></span><span></span><span></span></div>
</section>

<section class="about">
  <svg class="about-photo" width="290" height="432" viewBox="0 0 290 432">
    <defs><linearGradient id="aboutPhoto" x1="0" y1="0" x2="0" y2="1"><stop offset="0" stop-color="#6f8a78"/><stop offset=".6" stop-color="#8c9a9a"/><stop offset="1" stop-color="#e8eef0"/></linearGradient></defs>
    <path d="M37 0 C120 25 190 40 228 60 C265 150 285 250 286 345 L285 400 L0 432 C10 380 20 330 28 300 C35 200 40 100 37 0 Z" fill="url(#aboutPhoto)" role="img" aria-label="Close-up of a cracked car windshield"/>
  </svg>
  <h2 class="heading">About Harborline Auto Glass Repair</h2>
  <p>Lorem ipsum dolor sit amet, consectetur adipiscing elit, sed do eiusmod tempor incididunt ut labore et dolore magna aliqua. Ut enim ad minim veniam, quis nostrud exercitation ullamco laboris nisi ut aliquip ex ea commodo consequat. Duis aute irure dolor in reprehenderit in voluptate velit esse cillum dolore eu fugiat nulla pariatur. Excepteur sint occaecat cupidatat non proident, sunt in culpa qui officia deserunt mollit anim id est laborum.</p>
  <div class="btn">LEARN MORE</div>
</section>

<section class="services" role="img" aria-label="Faded workshop background">
  <h2 class="heading">Our Services</h2>

  <div class="card" style="left:112px;top:163px">
    <svg width="80" height="56" viewBox="0 0 80 56"><path d="M4 14 H76 L70 44 H10 Z" fill="none" stroke="#111" stroke-width="3"/><path d="M10 18 H70 L66 39 H14 Z" fill="#cfe8f8" stroke="#0a8ad6" stroke-width="2"/><line x1="40" y1="2" x2="40" y2="14" stroke="#111" stroke-width="3"/><line x1="33" y1="3" x2="47" y2="3" stroke="#111" stroke-width="3"/><line x1="28" y1="31" x2="32" y2="26" stroke="#0a8ad6" stroke-width="2"/><line x1="38" y1="31" x2="42" y2="26" stroke="#0a8ad6" stroke-width="2"/><line x1="48" y1="31" x2="52" y2="26" stroke="#0a8ad6" stroke-width="2"/></svg>
    <h3>Windshield Repair</h3>
    <p>Lorem ipsum dolor sit amet,<br>consectetur adipiscing elit, sed do</p>
    <div class="btn">LEARN MORE</div>
  </div>

  <div class="card" style="left:448px;top:163px">
    <svg width="80" height="56" viewBox="0 0 80 56"><path d="M8 12 Q40 4 72 12 Q76 28 72 44 Q40 52 8 44 Q4 28 8 12 Z" fill="none" stroke="#111" stroke-width="3"/><rect x="30" y="14" width="20" height="10" rx="2" fill="none" stroke="#111" stroke-width="3"/><line x1="36" y1="19" x2="44" y2="19" stroke="#0a8ad6" stroke-width="2"/></svg>
    <h3>Windshield Replacment</h3>
    <p>Lorem ipsum dolor sit amet,<br>consectetur adipiscing elit, sed do</p>
    <div class="btn">LEARN MORE</div>
  </div>

  <div class="card" style="left:785px;top:163px">
    <svg width="84" height="60" viewBox="0 0 84 60"><path d="M4 14 Q40 2 76 10 L70 20 L78 26 L70 56 Q40 46 16 52 Z" fill="none" stroke="#111" stroke-width="3"/><path d="M12 18 Q30 12 48 14 L42 40 Q28 40 18 44 Z" fill="none" stroke="#111" stroke-width="2"/><line x1="20" y1="26" x2="24" y2="20" stroke="#0a8ad6" stroke-width="2"/></svg>
    <h3>Rear Windshield Replacment</h3>
    <p>Lorem ipsum dolor sit amet,<br>consectetur adipiscing elit, sed do</p>
    <div class="btn">LEARN MORE</div>
  </div>

  <div class="card" style="left:112px;top:532px">
    <svg width="80" height="56" viewBox="0 0 80 56"><rect x="12" y="4" width="56" height="48" rx="3" fill="none" stroke="#111" stroke-width="3"/><path d="M12 24 L32 4" stroke="#111" stroke-width="2" fill="none"/><line x1="12" y1="28" x2="68" y2="28" stroke="#111" stroke-width="2"/><circle cx="44" cy="36" r="3" fill="none" stroke="#111" stroke-width="2"/><line x1="32" y1="28" x2="42" y2="34" stroke="#111" stroke-width="2"/></svg>
    <h3>Side Window Replacment</h3>
    <p>Lorem ipsum dolor sit amet,<br>consectetur adipiscing elit, sed do</p>
    <div class="btn">LEARN MORE</div>
  </div>

  <div class="card" style="left:448px;top:532px">
    <svg width="80" height="56" viewBox="0 0 80 56"><rect x="12" y="2" width="56" height="52" rx="3" fill="none" stroke="#111" stroke-width="3"/><line x1="12" y1="28" x2="68" y2="28" stroke="#111" stroke-width="2"/><path d="M40 8 V22 M34 14 L40 8 L46 14" stroke="#0a8ad6" stroke-width="2.5" fill="none"/><path d="M40 34 V48 M34 42 L40 48 L46 42" stroke="#0a8ad6" stroke-width="2.5" fill="none"/></svg>
    <h3>Car Window Replacment</h3>
    <p>Lorem ipsum dolor sit amet,<br>consectetur adipiscing elit, sed do</p>
    <div class="btn">LEARN MORE</div>
  </div>

  <div class="card" style="left:785px;top:532px">
    <svg width="80" height="60" viewBox="0 0 80 60"><path d="M10 58 V22 L30 4 H66 V58 Z" fill="none" stroke="#111" stroke-width="3"/><path d="M16 24 L32 10 H60 V28 H16 Z" fill="#cfe8f8" stroke="#0a8ad6" stroke-width="2"/><line x1="12" y1="38" x2="64" y2="38" stroke="#111" stroke-width="2"/><line x1="12" y1="46" x2="64" y2="46" stroke="#111" stroke-width="2"/><line x1="48" y1="34" x2="58" y2="34" stroke="#111" stroke-width="2"/></svg>
    <h3>Power Window Repair</h3>
    <p>Lorem ipsum dolor sit amet,<br>consectetur adipiscing elit, sed do</p>
    <div class="btn">LEARN MORE</div>
  </div>
</section>

<section class="testimonials">
  <h2 class="heading">Clients Testimonials</h2>
  <div class="arrow" style="left:68px;background:var(--blue)"><svg width="24" height="16" viewBox="0 0 24 16"><path d="M23 8 H2 M8 2 L2 8 L8 14" stroke="#fff" stroke-width="1.6" fill="none"/></svg></div>

  <div class="quote" style="left:113px">
    <svg class="qm" width="54" height="40" viewBox="0 0 54 40"><path d="M0 0 H22 V20 L14 38 H4 L10 20 H0 Z M30 0 H52 V20 L44 38 H34 L40 20 H30 Z" fill="#b9d3ea"/></svg>
    <p>"Lorem ipsum dolor sit amet, consectetur adipiscing elit, sed do eiusmod tempor incididunt ut labore et dolore magna aliqua. Ut enim ad minim veniam, quis nostrud exercitation ullamco laboris nisi ut aliquip ex ea commodo consequat. Duis aute irure dolor in reprehenderit in voluptate velit esse cillum dolore eu fugiat nulla pariatur. Excepteur sint occaecat cupidatat non proident, sunt in culpa qui officia deserunt mollit anim id est laborum."</p>
    <div class="avatar" role="img" aria-label="Client portrait"></div>
    <div class="who">Marcus Reed</div>
    <div class="role">Lorem ipsum dolor</div>
  </div>

  <div class="quote" style="left:623px">
    <svg class="qm" width="54" height="40" viewBox="0 0 54 40"><path d="M0 0 H22 V20 L14 38 H4 L10 20 H0 Z M30 0 H52 V20 L44 38 H34 L40 20 H30 Z" fill="#b9d3ea"/></svg>
    <p>"Lorem ipsum dolor sit amet, consectetur adipiscing elit, sed do eiusmod tempor incididunt ut labore et dolore magna aliqua. Ut enim ad minim veniam, quis nostrud exercitation ullamco laboris nisi ut aliquip ex ea commodo consequat. Duis aute irure dolor in reprehenderit in voluptate velit esse cillum dolore eu fugiat nulla pariatur. Excepteur sint occaecat cupidatat non proident, sunt in culpa qui officia deserunt mollit anim id est laborum."</p>
    <div class="avatar" role="img" aria-label="Client portrait" style="background:linear-gradient(135deg,#c9d6e2,#7f93a8)"></div>
    <div class="who">Daniel Ortiz</div>
    <div class="role">Lorem ipsum dolor</div>
  </div>

  <div class="arrow" style="left:1067px;background:#8d8d8d"><svg width="24" height="16" viewBox="0 0 24 16"><path d="M1 8 H22 M16 2 L22 8 L16 14" stroke="#fff" stroke-width="1.6" fill="none"/></svg></div>
</section>

<footer class="site-footer">
  <div class="brand"><span class="mark"></span><span class="name"><span class="l1">HARBORLINE</span><span class="l2">AUTO GLASS</span></span></div>
  <div class="social" aria-label="Social links"><span></span><span></span><span></span><span></span></div>

  <div class="fcol" style="left:417px">
    <h4>QUICK LINKS</h4>
    <ul class="links"><li>Home</li><li>About</li><li>Services</li><li>My appointment</li><li>Contact</li></ul>
  </div>

  <div class="fcol contact" style="left:619px;width:250px">
    <h4>CONTACT US</h4>
    <div class="row"><svg width="18" height="20" viewBox="0 0 18 20"><path d="M9 1 C4.5 1 2 4 2 7.5 C2 12 9 19 9 19 C9 19 16 12 16 7.5 C16 4 13.5 1 9 1 Z" fill="#fff"/><circle cx="9" cy="7.5" r="2.6" fill="#000"/></svg><span>Lorem ipsum dolor sit<br>amet, consectetur</span></div>
    <div class="row"><svg width="18" height="18" viewBox="0 0 18 18"><path d="M4 1 L7 5 L5 7.5 C6 10 8 12 10.5 13 L13 11 L17 14 L15 17 C8 17 1 10 1 3 Z" fill="#fff"/></svg><span>+1 (555) 014 2267</span></div>
    <div class="row"><svg width="18" height="14" viewBox="0 0 18 14"><rect x="0" y="1" width="18" height="12" rx="1" fill="#fff"/><path d="M1 2 L9 8 L17 2" stroke="#000" stroke-width="1.5" fill="none"/></svg><span>info@harborlineautoglass.com</span></div>
  </div>

  <div class="fcol" style="left:863px">
    <h4>NEWSLETTER</h4>
  </div>
  <div class="news"><span>Enter email</span><div class="go"><svg width="16" height="12" viewBox="0 0 16 12"><rect width="16" height="12" rx="1" fill="#fff"/><path d="M1 1 L8 6.5 L15 1" stroke="#0d5a9c" stroke-width="1.5" fill="none"/></svg></div></div>

  <div class="copy">©Copyrights 2022 Harborline Auto Glass &nbsp;| &nbsp;&nbsp; All Rights Reserved</div>
</footer>

</body>
</html>
```